New Business Card Design Project

Use the flyer uploaded and website www.brightoakbuilders.com for inspiration.
List Our Services on Backside of business cards
Marcus Delling
Harborline Builders Inc.
Licensed General Contractors
858-471-6093

Contact Information for Business Card

Use the flyer uploaded and website www.brightoakbuilders.com for inspiration. List Our Services on Backside of business cards Marcus Delling Harborline Builders Inc. Licensed General Contractors 858-471-6093

```html
<!DOCTYPE html>
<html lang="en">
<head>
<meta charset="utf-8">
<title>Harborline Builders Inc. – Business Card</title>
<link rel="stylesheet" href="https://fonts.googleapis.com/css2?family=Cinzel:wght@400;600&family=Roboto:wght@400;500&display=swap">
<style>
  :root {
    --bg: #2b2b2b;
    --card-black: #111111;
    --card-blue: #3583c8;
    --text-white: #ffffff;
    --accent-red: #e3202c;
    --bullet-blue: #3583c8;
    --muted-line: #3a3a3a;
  }
  * { box-sizing: border-box; margin: 0; padding: 0; }
  html, body { width: 1200px; height: 689px; overflow: hidden; }
  body {
    background: var(--bg);
    font-family: "Roboto", Arial, sans-serif;
    position: relative;
  }
  .card {
    position: absolute;
    top: 190px;
    width: 540px;
    height: 309px;
    border-radius: 22px;
    overflow: hidden;
    background: var(--card-black);
    box-shadow: 0 14px 30px rgba(0,0,0,0.45);
  }
  .card--back { left: 30px; }
  .card--front { left: 630px; }

  /* Back: services list */
  .services {
    position: absolute;
    left: 42px;
    top: 50px;
    list-style: none;
    color: var(--text-white);
    font-size: 17px;
    line-height: 23.5px;
    font-weight: 500;
  }
  .services li::before {
    content: "";
    display: inline-block;
    width: 6px; height: 6px;
    border-radius: 50%;
    background: var(--bullet-blue);
    margin-right: 10px;
    vertical-align: middle;
  }
  .back-lines { position: absolute; inset: 0; }

  /* Front */
  .front-shape { position: absolute; inset: 0; }
  .contact-block {
    position: absolute;
    left: 40px;
    top: 62px;
    color: var(--text-white);
  }
  .person-name {
    font-family: "Cinzel", Georgia, serif;
    font-weight: 600;
    font-size: 30px;
    letter-spacing: 1px;
    margin-bottom: 30px;
  }
  .contact-list { list-style: none; font-size: 16px; line-height: 26px; }
  .contact-list li { display: flex; align-items: center; gap: 10px; }
  .contact-list svg { width: 16px; height: 16px; flex: none; }

  .brand {
    position: absolute;
    right: 28px;
    top: 92px;
    width: 200px;
    text-align: center;
    color: var(--text-white);
    font-family: "Roboto", Arial, sans-serif;
    font-weight: 400;
    font-size: 19px;
    letter-spacing: 1.5px;
    text-transform: uppercase;
    line-height: 26px;
  }
  .company-lines {
    position: absolute;
    right: 28px;
    top: 200px;
    width: 220px;
    text-align: center;
    color: var(--accent-red);
    font-size: 16px;
    line-height: 22px;
    font-weight: 500;
  }
</style>
</head>
<body>

  <section class="card card--back" aria-label="Business card back">
    <svg class="back-lines" viewBox="0 0 540 309" aria-hidden="true">
      <polyline points="330,309 330,200 540,130" fill="none" stroke="var(--muted-line)" stroke-width="2"/>
    </svg>
    <ul class="services">
      <li>Remodel: Kitchen &amp; Bath</li>
      <li>Painting: Interior &amp; Exterior</li>
      <li>Flooring: Carpet, Vinyl, Wood</li>
      <li>Window &amp; Door Replacement</li>
      <li>Plumbing: Repairs &amp; Upgrades</li>
      <li>Energy-Efficient Upgrades</li>
      <li>Deck &amp; Patio Construction</li>
      <li>Water &amp; Mold Damage</li>
      <li>Garage Renovation</li>
    </ul>
  </section>

  <section class="card card--front" aria-label="Business card front">
    <svg class="front-shape" viewBox="0 0 540 309" preserveAspectRatio="none" aria-hidden="true">
      <polygon points="0,0 330,0 250,185 320,309 0,309" fill="var(--card-blue)"/>
    </svg>

    <div class="contact-block">
      <h1 class="person-name">Marcus Delling</h1>
      <ul class="contact-list">
        <li>
          <svg viewBox="0 0 24 24" fill="var(--text-white)" aria-hidden="true"><path d="M6.6 10.8a15 15 0 0 0 6.6 6.6l2.2-2.2a1 1 0 0 1 1-.25 11.4 11.4 0 0 0 3.6.57 1 1 0 0 1 1 1V20a1 1 0 0 1-1 1A17 17 0 0 1 3 4a1 1 0 0 1 1-1h3.5a1 1 0 0 1 1 1c0 1.25.2 2.45.57 3.57a1 1 0 0 1-.25 1z"/></svg>
          858-471-6093
        </li>
        <li>
          <svg viewBox="0 0 24 24" fill="var(--text-white)" aria-hidden="true"><path d="M2 5h20v14H2z" fill="none" stroke="#fff" stroke-width="2"/><path d="M2 5l10 8 10-8" fill="none" stroke="#fff" stroke-width="2"/></svg>
          info@harborlinebuilders.com
        </li>
        <li>
          <svg viewBox="0 0 24 24" fill="none" stroke="var(--text-white)" stroke-width="2" aria-hidden="true"><circle cx="12" cy="12" r="10"/><path d="M2 12h20M12 2a15 15 0 0 1 0 20M12 2a15 15 0 0 0 0 20"/></svg>
          www.brightoakbuilders.com
        </li>
      </ul>
    </div>

    <div class="brand">Harborline Builders</div>

    <div class="company-lines">
      <p>Harborline Builders Inc.</p>
      <p>Licensed General Contractors</p>
    </div>
  </section>

</body>
</html>
```